Help our Sugar Loom find our winning design! We're looking for a business card....

We’re a Sugar Loom in NY specializing in custom-made cakes and unique desserts.
Our cakes combine flavor and art, each designed to match customer’s special event and theme.
We’d like a unique business card with a clean design that will combine French chic and artistic look & feel.
We’d like to differentiate ourselves from standard bakeries, please don’t offer cupcake images :-)
Our logo is peach-pink and brown and we’d love to use these colors ( . Another color that can be added is gold - or feel free to suggest!

Target Market(s)

Women, ages 25-55

Industry/Entity Type

Boutique

Contact Information for Business Card

Text on card:
Logo
Sugar Loom by Dana Welch

www.sugarloomsweets.com
hello@sugarloom.com
(516) 555-0147
F – sugarloomnyc
IG - sugarloom_ny

Font styles to use
Sans Serif
Script

Requirements
Must have
• Logo
• Clean look
• French chic and artistic look & feel.
Nice to have
• Damask pattern
Should not have
• Cupcake images

```html
<!DOCTYPE html>
<html lang="en">
<head>
<meta charset="utf-8">
<title>Sugar Loom — Business Card</title>
<link rel="stylesheet" href="https://fonts.googleapis.com/css2?family=Great+Vibes&family=Open+Sans:wght@400;600&display=swap">
<style>
  :root {
    --backdrop: #e4e4e4;
    --cocoa: #3a3030;
    --cocoa-deep: #2e2626;
    --fuchsia: #e0177e;
    --peach: #eaa08f;
    --peach-soft: #f6ddd8;
    --cream: #ffffff;
    --ink: #3b3333;
    --gold-light: #e9c86a;
    --gold-dark: #8a6418;
  }
  * { box-sizing: border-box; margin: 0; padding: 0; }
  html, body { width: 1200px; height: 852px; overflow: hidden; }
  body {
    background: var(--backdrop);
    font-family: "Open Sans", Arial, sans-serif;
    color: var(--ink);
    position: relative;
  }
  .card {
    position: absolute;
    top: 277px;
    width: 520px;
    height: 298px;
    border-radius: 18px;
    overflow: hidden;
    box-shadow: 0 4px 14px rgba(0,0,0,0.18);
  }
  /* Front */
  .card--front { left: 50px; }
  .front__pattern {
    position: absolute; inset: 0;
    background: linear-gradient(135deg, var(--cocoa) 0%, var(--cocoa-deep) 100%);
  }
  .front__band {
    position: absolute; left: 0; right: 0; top: 122px; height: 54px;
    background: var(--fuchsia);
    border-top: 2px solid #f36bb2;
    border-bottom: 2px solid #f36bb2;
  }
  .front__cartouche {
    position: absolute; left: 125px; top: 70px; width: 270px; height: 158px;
    background: var(--cream);
    border: 3px solid var(--peach);
    border-radius: 70px 70px 60px 60px / 50px 50px 50px 50px;
    box-shadow: 0 2px 6px rgba(0,0,0,0.25);
    display: flex; align-items: center; justify-content: center;
  }
  .brand-name {
    font-family: "Great Vibes", cursive;
    color: var(--ink);
    font-weight: 400;
    white-space: nowrap;
  }
  .front__cartouche .brand-name { font-size: 54px; }

  /* Back */
  .card--back { left: 630px; background: var(--cream); }
  .back__flourish {
    position: absolute; left: 40px; top: 30px; width: 150px; height: 190px;
    border-radius: 50%;
    background: radial-gradient(ellipse at center, var(--peach-soft) 0%, rgba(246,221,216,0) 70%);
    opacity: 0.8;
  }
  .back__logo {
    position: absolute; right: 28px; top: 26px; width: 250px; height: 96px;
    border: 2px solid var(--peach);
    border-radius: 60px 60px 48px 48px / 40px 40px 40px 40px;
    display: flex; align-items: center; justify-content: center;
  }
  .back__logo .brand-name { font-size: 44px; }
  .back__rule {
    position: absolute; left: 190px; right: 18px; top: 150px; height: 3px;
    background: linear-gradient(90deg, var(--gold-dark), var(--gold-light) 60%, var(--gold-dark));
  }
  .owner { position: absolute; left: 36px; top: 150px; }
  .owner__intro { font-size: 15px; letter-spacing: 0.2px; }
  .owner__name {
    font-family: "Great Vibes", cursive;
    font-size: 30px; line-height: 1.05;
  }
  .contacts {
    position: absolute; left: 36px; top: 222px;
    list-style: none; font-size: 13.5px; line-height: 21px;
  }
  .contacts li, .socials li { display: flex; align-items: center; gap: 8px; }
  .contacts svg { width: 13px; height: 13px; fill: var(--ink); flex: none; }
  .socials {
    position: absolute; right: 24px; top: 166px;
    list-style: none; font-size: 13.5px; line-height: 21px;
  }
  .socials .mark {
    width: 11px; height: 11px; border-radius: 2px; background: var(--ink); flex: none;
  }
</style>
</head>
<body>
  <section class="card card--front" aria-label="Card front">
    <div class="front__pattern" role="img" aria-label="Brown damask pattern background"></div>
    <div class="front__band"></div>
    <div class="front__cartouche">
      <span class="brand-name">Sugar Loom</span>
    </div>
  </section>

  <section class="card card--back" aria-label="Card back">
    <div class="back__flourish" role="img" aria-label="Faint pink floral flourish"></div>
    <div class="back__logo">
      <span class="brand-name">Sugar Loom</span>
    </div>
    <div class="back__rule"></div>

    <div class="owner">
      <p class="owner__intro">Sugar Loom by</p>
      <p class="owner__name">Dana Welch</p>
    </div>

    <ul class="contacts">
      <li>
        <svg viewBox="0 0 16 16" aria-hidden="true"><path d="M3 1h3l1.5 4-2 1.3a9 9 0 0 0 4.2 4.2L11 8.5l4 1.5v3a2 2 0 0 1-2 2A12 12 0 0 1 1 3a2 2 0 0 1 2-2z"/></svg>
        (516) 555-0147
      </li>
      <li>
        <svg viewBox="0 0 16 16" aria-hidden="true"><path d="M1 3h14v10H1z M2 4l6 5 6-5" stroke="#fff" stroke-width="1.2"/></svg>
        hello@sugarloom.com
      </li>
      <li>
        <svg viewBox="0 0 16 16" aria-hidden="true"><circle cx="8" cy="8" r="7"/><path d="M1 8h14M8 1c3 3 3 11 0 14M8 1c-3 3-3 11 0 14" stroke="#fff" stroke-width="1" fill="none"/></svg>
        www.sugarloomsweets.com
      </li>
    </ul>

    <ul class="socials">
      <li><span class="mark"></span>sugarloomnyc</li>
      <li><span class="mark"></span>sugarloom_ny</li>
    </ul>
  </section>
</body>
</html>
```